Business Card Design for Varomir Facility Services

We are looking for a Business Card Design for the Company "Varomir Facility Services."
Front side:
- Company Logo (small)
- Company Name, address, pohone, website and personal data.
- white background, for text e.g. company colors (blue or green like in the logo)
Please use following data:
Company data:
Varomir Facility Services Kostelac
Birkenhaldweg 14
6330 Cham
www.varomir-fs.ch
Person data:
Tarik Kostelac
Geschäftsführer
+41 76 519 47 83
info@varomir-fs.ch
Back side:
could be colored in blue or green
please use a big logo sing and some smaller icons to say what is all beeing offered in facility services, like cleaning, maintenance cleaning
industrial cleaning, caretaking, gardening, disposal. There is no need for everyone of the icons if there are similar or an icon is standing for more of them.
colors to use:
blue: HEX 246BB0
green: HEX 52B33E

```html
<!DOCTYPE html>
<html lang="de">
<head>
<meta charset="utf-8">
<title>Varomir Facility Services – Business Card</title>
<link href="https://fonts.googleapis.com/css2?family=Source+Sans+3:wght@400;600&display=swap" rel="stylesheet">
<style>
  :root{
    --blue:#246bb0;
    --green:#5ab946;
    --ink:#0f1c22;
    --paper:#ffffff;
    --mist:#e3e8ec;
    --bg:#ffffff;
  }
  *{margin:0;padding:0;box-sizing:border-box}
  html,body{width:1200px;height:960px;overflow:hidden;background:var(--bg)}
  body{position:relative;font-family:"Source Sans 3",sans-serif}
  .card{position:absolute;left:286px;width:629px;height:359px;background:var(--paper);
        box-shadow:0 2px 6px rgba(0,0,0,.28);overflow:hidden}
  .card--front{top:109px}
  .card--back{top:492px}
  .card__shapes{position:absolute;inset:0}
  .brand{position:absolute;color:var(--blue);font-weight:600;display:flex;align-items:center;gap:10px}
  .brand__mark{width:14px;height:14px;background:var(--green);flex:none}
  .card--front .brand{left:67px;top:74px;font-size:27px;letter-spacing:.3px}
  .card--back .brand{left:0;width:320px;top:108px;justify-content:center;text-align:center;
        font-size:34px;line-height:1.08;flex-direction:column;gap:12px}
  .person{position:absolute;left:66px;top:218px;color:#fff}
  .person__name{font-size:23px;font-weight:600;line-height:1.2}
  .person__role{font-size:18px;font-weight:400;margin-top:2px}
  .contacts{position:absolute;left:290px;top:194px;list-style:none;color:#fff;font-size:16px}
  .contacts li{display:flex;align-items:center;height:26.2px}
  .contacts svg{width:17px;height:17px;margin-right:16px;fill:var(--green);flex:none}
  .services{position:absolute;left:366px;top:99px;list-style:none;color:#fff;font-size:17px}
  .services li{display:flex;align-items:center;height:26.3px}
  .services svg{width:15px;height:15px;margin-right:8px;fill:#fff;flex:none}
</style>
</head>
<body>

<section class="card card--front" aria-label="Visitenkarte Vorderseite">
  <svg class="card__shapes" viewBox="0 0 629 359" aria-hidden="true">
    <path d="M517 92 Q517 84 526 86 L548 157 L544 157 Z" fill="var(--mist)"/>
    <rect x="0" y="157" width="600" height="180" fill="var(--ink)"/>
    <path d="M547 67 L629 67 L629 337 L598 337 Q577 337 572 317 L533 82 Q531 67 547 67 Z" fill="var(--green)"/>
  </svg>
  <div class="brand"><span class="brand__mark"></span>Varomir Facility Services</div>
  <div class="person">
    <div class="person__name">Tarik Kostelac</div>
    <div class="person__role">Geschäftsführer</div>
  </div>
  <ul class="contacts">
    <li><svg viewBox="0 0 24 24"><path d="M6.6 10.8c1.4 2.8 3.8 5.1 6.6 6.6l2.2-2.2c.3-.3.7-.4 1-.2 1.1.4 2.3.6 3.6.6.6 0 1 .4 1 1V20c0 .6-.4 1-1 1C10.6 21 3 13.4 3 4c0-.6.4-1 1-1h3.5c.6 0 1 .4 1 1 0 1.3.2 2.5.6 3.6.1.3 0 .7-.2 1z"/></svg>+41 76 519 47 83</li>
    <li><svg viewBox="0 0 24 24"><path d="M2 5h20v14H2z M3.5 6.5 12 13l8.5-6.5" fill="var(--green)"/><path d="M3 6l9 7 9-7" fill="none" stroke="var(--ink)" stroke-width="1.6"/></svg>info@varomir-fs.ch</li>
    <li><svg viewBox="0 0 24 24"><circle cx="12" cy="12" r="10"/><path d="M5 8q4 1 5 5M14 3q-1 5 4 7M9 21q1-5 7-6" fill="none" stroke="var(--ink)" stroke-width="1.6"/></svg>www.varomir-fs.ch</li>
    <li><svg viewBox="0 0 24 24"><path d="M12 2a6 6 0 0 1 6 6c0 4-6 10-6 10S6 12 6 8a6 6 0 0 1 6-6zm0 4a2 2 0 1 0 0 4 2 2 0 0 0 0-4z"/><ellipse cx="12" cy="20.5" rx="8" ry="2" fill="none" stroke="var(--green)" stroke-width="1.6"/></svg>Birkenhaldweg 14, 6330 Cham</li>
  </ul>
</section>

<section class="card card--back" aria-label="Visitenkarte Rückseite">
  <svg class="card__shapes" viewBox="0 0 629 359" aria-hidden="true">
    <path d="M300 46 L629 46 L629 316 L360 316 Q337 316 333 293 L292 56 Q291 46 300 46 Z" fill="var(--green)"/>
  </svg>
  <div class="brand"><span class="brand__mark"></span>Varomir<br>Facility Services</div>
  <ul class="services">
    <li><svg viewBox="0 0 24 24"><path d="M12 1 14 10 23 12 14 14 12 23 10 14 1 12 10 10Z"/></svg>Like cleaning</li>
    <li><svg viewBox="0 0 24 24"><path d="M12 1 14 10 23 12 14 14 12 23 10 14 1 12 10 10Z"/></svg>Maintenance cleaning</li>
    <li><svg viewBox="0 0 24 24"><path d="M12 1 14 10 23 12 14 14 12 23 10 14 1 12 10 10Z"/></svg>Industrial cleaning</li>
    <li><svg viewBox="0 0 24 24"><path d="M12 1 14 10 23 12 14 14 12 23 10 14 1 12 10 10Z"/></svg>Caretaking</li>
    <li><svg viewBox="0 0 24 24"><path d="M12 1 14 10 23 12 14 14 12 23 10 14 1 12 10 10Z"/></svg>Gardening</li>
    <li><svg viewBox="0 0 24 24"><path d="M12 1 14 10 23 12 14 14 12 23 10 14 1 12 10 10Z"/></svg>Disposal</li>
  </ul>
</section>

</body>
</html>
```